TLK Electricial Contracting Services

Hi guys, after a design for my small electrical company, have logo design files to be incorporated into the layout, the basic concept is electrical contracting services for residential, commercial, industrial & data services, image is clean clear and strong,

Card format is to have a nice clean logo on front,with maybe the Residential – commercial – industrial - data, followed with licensed & insured, followed by contact details on backside of the card.

Target Market(s)

Residential, commercial, industrial sectors.

Industry/Entity Type

Electrical

Contact Information for Business Card

TLK logo,
Residential – commercial – industrial - data
REC: 61307
Email: tlk@vornamail.net.au
Phone: 0487 352 019

Requirements
Must have
• Clean & strong design.
Nice to have
• If possible, I would like the logo colours inverted so the text is orange and the background is black on the front of the card, then the backside of the card be the reverse colour
Should not have
• No Sparks, lightning bolts,

```html
<!DOCTYPE html>
<html lang="en">
<head>
<meta charset="utf-8">
<title>TLK Electricial Contracting Services – Business Card</title>
<link rel="stylesheet" href="https://fonts.googleapis.com/css2?family=Lato:wght@400;700&display=swap">
<style>
  :root {
    --backdrop: #3b3b3b;
    --card-black: #111111;
    --brand-orange: #f4822a;
    --ink-black: #0d0d0d;
    --text-white: #f2f2f2;
    --text-grey: #9a9a9a;
  }
  * { margin: 0; padding: 0; box-sizing: border-box; }
  html, body { width: 1200px; height: 900px; overflow: hidden; }
  body {
    background: var(--backdrop);
    font-family: "Lato", Arial, sans-serif;
    position: relative;
  }
  .card {
    position: absolute;
    width: 295px;
    height: 507px;
    border-radius: 14px;
    text-align: center;
  }
  .card--front { left: 310px; top: 194px; background: var(--card-black); color: var(--text-white); }
  .card--back { left: 632px; top: 195px; background: var(--brand-orange); color: var(--ink-black); }

  .brand { position: absolute; left: 0; right: 0; font-weight: 700; }
  .brand__initials { display: block; font-size: 78px; line-height: 1; letter-spacing: 1px; }
  .brand__name { display: block; font-size: 15px; letter-spacing: 0.3px; margin-top: 4px; }
  .card--front .brand { top: 68px; color: var(--brand-orange); }
  .card--back .brand { top: 208px; color: var(--ink-black); }

  .services {
    position: absolute; top: 200px; left: 0; right: 0;
    list-style: none; font-size: 15px; line-height: 19px; text-transform: uppercase;
  }
  .licence { position: absolute; top: 296px; left: 0; right: 0; font-size: 15px; }
  .licence__label { color: var(--brand-orange); }

  .contact {
    position: absolute; top: 419px; left: 0; right: 0;
    list-style: none; color: var(--text-grey); font-size: 16px; line-height: 21px;
  }
  .contact__icon { width: 12px; height: 12px; vertical-align: -1px; margin-right: 4px; fill: var(--brand-orange); }
</style>
</head>
<body>
  <section class="card card--front" aria-label="Card front">
    <div class="brand">
      <span class="brand__initials">TLK</span>
      <span class="brand__name">Tom Lyle Kirby Electrical</span>
    </div>
    <ul class="services">
      <li>Residential</li>
      <li>Commercial</li>
      <li>Industrial</li>
      <li>Data</li>
    </ul>
    <p class="licence"><span class="licence__label">REC:</span> 61307</p>
    <ul class="contact">
      <li><svg class="contact__icon" viewBox="0 0 12 12" aria-hidden="true"><path d="M1 4.5C1 3 3 2 6 2s5 1 5 2.5V5.5H8.5V4.2H3.5V5.5H1Z"/><path d="M3 6h6l1.5 4h-9Z"/></svg>0487 352 019</li>
      <li><svg class="contact__icon" viewBox="0 0 12 12" aria-hidden="true"><path d="M1 3h10v6.5H1Z"/><path d="M1 3l5 3.8L11 3" fill="none" stroke="#111" stroke-width="1"/></svg>tlk@vornamail.net.au</li>
    </ul>
  </section>

  <section class="card card--back" aria-label="Card back">
    <div class="brand">
      <span class="brand__initials">TLK</span>
      <span class="brand__name">Tom Lyle Kirby Electrical</span>
    </div>
  </section>
</body>
</html>
```